Need Business Card for our Real Estate Business with Sales Executive's Picture

PANTONE 484 C ( RED)

PANTONE 2766 C ( BLUE

Industry/Entity Type

Real Estate

Contact Information for Business Card

Name, Mobile, email, & picture of Person
Agency Phone, address, Web address

Requirements
Must have
• Our Logo Colours, Agent Picture,

```html
<!DOCTYPE html>
<html lang="en">
<head>
<meta charset="utf-8">
<title>Meridian Realty – Business Card</title>
<link rel="stylesheet" href="https://fonts.googleapis.com/css2?family=Amaranth:wght@400;700&family=Open+Sans:wght@400;600&display=swap">
<style>
  :root {
    --canvas-bg: #e9e6e1;
    --card-bg: #f7f6f4;
    --brand-blue: #1b2658;
    --brand-red: #a8322a;
    --name-gold: #dccbb0;
    --title-light: #e8e8ee;
    --text-navy: #1e2a5a;
    --photo-top: #c9c3ba;
    --photo-bottom: #2a3560;
  }
  * { margin: 0; padding: 0; box-sizing: border-box; }
  html, body {
    width: 1200px; height: 1054px; overflow: hidden;
    background: var(--canvas-bg);
  }
  .card {
    position: absolute; left: 100px; top: 224px;
    width: 1000px; height: 606px;
    background: var(--card-bg);
    overflow: hidden;
    box-shadow: 0 10px 30px rgba(0,0,0,0.18);
    font-family: "Open Sans", sans-serif;
  }
  .header-band {
    position: absolute; left: 0; top: 0; width: 100%; height: 160px;
    background: var(--brand-blue);
  }
  .accent-rule {
    position: absolute; left: 0; top: 170px; width: 100%; height: 10px;
    background: var(--brand-red);
  }
  .person {
    position: absolute; right: 46px; top: 52px; text-align: right;
  }
  .person__name {
    font-family: "Amaranth", sans-serif; font-weight: 700;
    font-size: 34px; color: var(--name-gold); line-height: 1.1;
  }
  .person__title {
    font-size: 23px; color: var(--title-light); margin-top: 6px;
  }
  .brand {
    position: absolute; left: 60px; top: 222px;
    display: flex; align-items: center; gap: 22px;
  }
  .brand__mark { width: 44px; height: 44px; background: var(--brand-blue); }
  .brand__name {
    font-size: 56px; font-weight: 600; color: var(--brand-blue);
    letter-spacing: 1px;
  }
  .contacts {
    position: absolute; left: 62px; top: 378px; list-style: none;
  }
  .contacts li {
    display: flex; align-items: center; gap: 14px;
    font-size: 23px; color: var(--text-navy); height: 33px;
  }
  .contacts svg { width: 20px; height: 20px; fill: var(--brand-red); flex: none; }
  .address {
    position: absolute; left: 60px; top: 520px;
    font-size: 23px; color: var(--text-navy);
  }
  .portrait {
    position: absolute; left: 650px; top: 245px; width: 350px; height: 361px;
    background: linear-gradient(180deg, var(--photo-top) 0%, #b9a590 45%, var(--photo-bottom) 100%);
  }
</style>
</head>
<body>
  <div class="card">
    <div class="header-band"></div>
    <div class="accent-rule"></div>

    <div class="person">
      <p class="person__name">Marianne Holt</p>
      <p class="person__title">Managing Director</p>
    </div>

    <div class="brand">
      <span class="brand__mark"></span>
      <span class="brand__name">Meridian Realty</span>
    </div>

    <ul class="contacts">
      <li>
        <svg viewBox="0 0 20 20"><path d="M6 1h8a2 2 0 0 1 2 2v14a2 2 0 0 1-2 2H6a2 2 0 0 1-2-2V3a2 2 0 0 1 2-2zm0 3v10h8V4zm4 11.5a1 1 0 1 0 0 2 1 1 0 0 0 0-2z"/></svg>
        555.214.3087
      </li>
      <li>
        <svg viewBox="0 0 20 20"><path d="M2 6c0-2 3-3 8-3s8 1 8 3v2h-4V6.5C12 6 8 6 6 6.5V8H2zm3 3h10l3 8H2zm5 2a2.5 2.5 0 1 0 0 5 2.5 2.5 0 0 0 0-5z"/></svg>
        555-310-4476
      </li>
      <li>
        <svg viewBox="0 0 20 20"><path d="M1 4h18v12H1zm2 2v.4l7 5 7-5V6zm0 2.8V14h14V8.8l-7 5z"/></svg>
        meridianrealty.example
      </li>
      <li>
        <svg viewBox="0 0 20 20"><path d="M10 1a9 9 0 1 0 0 18 9 9 0 0 0 0-18zm-1 2.1V6H6.3A7 7 0 0 1 9 3.1zm2 0A7 7 0 0 1 13.7 6H11zM3.3 8h5.7v3H3.1a7 7 0 0 1 .2-3zm7.7 0h5.7a7 7 0 0 1 .2 3H11zM3.6 13H9v3.9A7 7 0 0 1 3.6 13zm7.4 0h5.4a7 7 0 0 1-5.4 3.9z"/></svg>
        mholt@meridianrealty.example
      </li>
    </ul>

    <p class="address">418 Alder Ave #210, Fairview, CO 80000</p>

    <div class="portrait" role="img" aria-label="Portrait photo of the agent in a navy suit and tie"></div>
  </div>
</body>
</html>
```